Pizza Coupon App Design Project

*******This project will have a guaranteed payout once I see that there is quality work being designed*********

I require the design (no coding) of 4 vertical screens (the screen will not change for horizontal orientation) for Zentrix and Orbalis. The highest res should be used so it can be scaled for older generation phones.

The mobile app will be used to access pizza coupons.

I do not have a specific style or look that I am going for, although I do not want a childish design (e.g. comic sans). The main requirements are for it to be very easy for users to understand and navigate and to be clean and professional.

I am happy if you only produce a design of the main and store selection screens to which I will give feedback before continuing to design the remaining screens.

The selected artist must be flexible in adapting the final design slightly after the contest is completed, during the app development process (maybe a few small modifications over a month or so).
Please do not include any copyrighted images in your deliverables. I must be the sole owner of the graphics once I have paid for them.

I have included attachments which show the process flow and the screen requirements so that will give you the detail you need to design them. I have also included the logo to assist you in your design., *******This project is now guaranteed *********

I have included attachments which show the process flow and the screen requirements so that will give you the detail you need to design them. I have also included the logo to assist you in your design., *******This project will have a guaranteed payout once I see that there is quality work being designed*********

I have included attachments which show the process flow and the screen requirements so that will give you the detail you need to design them. I have also included the logo to assist you in your design.

Reason: Still looking for the perfect design! ******Project is now guaranteed******

******Project is now guaranteed******

Reason: Starting to get some great designs, we are getting much closer! Keep it up.

Target Market(s)

students and 18-30 year olds - People who want cheap meals and people who order pizza online., students and 18-30 year olds - People who want cheap meals and people who order pizza online., students and 18-30 year olds - People who want cheap meals and people who order pizza online.

Industry/Entity Type

Store

Requirements
Must have
• Must have requirements are listed in the attached documents., Must have requirements are listed in the attached documents., Must have requirements are listed in the attached documents.

```html
<!DOCTYPE html>
<html lang="en">
<head>
<meta charset="utf-8">
<title>Pizza Coupons – Store Offers</title>
<link href="https://fonts.googleapis.com/css2?family=Open+Sans:wght@400;600;700&family=PT+Sans:wght@400;700&display=swap" rel="stylesheet">
<style>
  :root {
    --stage: #e6e6e6;
    --screen-bg: #f2efec;
    --ad-band: #6e6e6e;
    --ad-text: #9a9a9a;
    --ink: #2b2b2b;
    --icon: #4a4a4a;
    --coupon-light: #f7ac55;
    --coupon-mid: #f29a3e;
    --coupon-edge: #e4872c;
    --coupon-text: #c2572b;
    --stub: #cf5a36;
    --stub-dark: #a8401f;
    --stub-ink: #5b1f0f;
    --track: #3a3a3a;
    --thumb: #c7594a;
    --badge: #6d4a2c;
  }
  * { box-sizing: border-box; margin: 0; padding: 0; }
  html, body { width: 1200px; height: 1000px; overflow: hidden; }
  body { background: var(--stage); font-family: "Open Sans", sans-serif; }

  .app-screen {
    position: absolute; left: 280px; top: 20px;
    width: 640px; height: 960px;
    background: var(--screen-bg);
    overflow: hidden;
    box-shadow: 0 2px 12px rgba(0,0,0,.12);
  }
  .ad-banner {
    height: 200px; background: var(--ad-band);
    display: flex; align-items: center; justify-content: center;
    font-family: "PT Sans", sans-serif; font-size: 42px; color: var(--ad-text);
    letter-spacing: 1px;
  }
  .filter-select {
    position: absolute; left: 330px; top: 228px; width: 235px; height: 50px;
    border: 2px solid #555; border-radius: 14px; overflow: hidden;
    display: flex; background: linear-gradient(#ffffff, #dcdcdc);
  }
  .filter-select .label { flex: 1; font-size: 25px; line-height: 46px; padding-left: 14px; color: var(--ink); }
  .filter-select .funnel {
    width: 62px; background: linear-gradient(#8a8a8a, #5e5e5e);
    display: flex; align-items: center; justify-content: center;
  }
  .scroll-track {
    position: absolute; left: 598px; top: 232px; width: 12px; height: 600px;
    background: var(--track); border-radius: 6px;
  }
  .scroll-thumb { height: 110px; background: var(--thumb); border-radius: 6px; }

  .store-heading {
    position: absolute; left: 18px; top: 290px;
    display: flex; align-items: center; gap: 14px;
    font-size: 36px; color: var(--ink);
  }

  .coupon-row { position: absolute; left: 8px; width: 575px; height: 122px; display: flex; align-items: center; }
  .row-icons { width: 58px; display: flex; flex-direction: column; align-items: center; gap: 6px; }
  .coupon {
    flex: 1; height: 100%; display: flex; border-radius: 6px; overflow: hidden;
    box-shadow: 0 3px 5px rgba(0,0,0,.18);
  }
  .coupon-body {
    flex: 1; position: relative;
    background: linear-gradient(var(--coupon-light), var(--coupon-mid));
    border: 2px solid var(--coupon-edge); border-right: none;
    display: flex; align-items: center; padding: 0 22px;
    color: var(--coupon-text); font-weight: 700;
  }
  .coupon-body::before {
    content: ""; position: absolute; inset: 8px 0 8px 8px;
    border: 1px dashed rgba(194,87,43,.35); border-right: none; border-radius: 4px;
  }
  .deal { font-size: 27px; line-height: 1.05; width: 130px; }
  .op { font-size: 30px; width: 60px; text-align: center; }
  .bonus { display: flex; flex-direction: column; align-items: center; }
  .free-tag {
    background: var(--badge); color: #f7d9a8; font-size: 11px; font-weight: 700;
    padding: 1px 5px; margin-top: 2px; letter-spacing: .5px;
  }
  .discount { text-align: center; color: #5a3a20; }
  .discount .pct { font-size: 28px; line-height: 1; }
  .discount .word { font-size: 15px; font-weight: 600; }
  .coupon-stub {
    width: 150px; background: linear-gradient(var(--stub), var(--stub-dark));
    border-left: 3px dashed rgba(255,255,255,.25);
    display: flex; align-items: center; justify-content: center;
  }

  .nav-back { position: absolute; left: 28px; top: 885px; }
  .nav-settings { position: absolute; left: 572px; top: 845px; }
</style>
</head>
<body>
<main class="app-screen">
  <header class="ad-banner">Advertising</header>

  <div class="filter-select">
    <span class="label">Delivery</span>
    <span class="funnel">
      <svg width="30" height="30" viewBox="0 0 30 30"><path d="M3 5h24l-9 10v9l-6 3V15z" fill="none" stroke="#222" stroke-width="2.4" stroke-linejoin="round"/></svg>
    </span>
  </div>

  <div class="scroll-track"><div class="scroll-thumb"></div></div>

  <h1 class="store-heading">
    <svg width="46" height="40" viewBox="0 0 46 40"><path d="M4 4h38l3 10H1z" fill="var(--icon)"/><path d="M6 16h34v22H6z" fill="none" stroke="var(--icon)" stroke-width="3"/><rect x="12" y="22" width="22" height="8" fill="var(--icon)"/></svg>
    <span style="font-weight:400">STORE 1</span>
  </h1>

  <!-- Offer 1 -->
  <section class="coupon-row" style="top:340px">
    <div class="row-icons">
      <svg width="36" height="36" viewBox="0 0 36 36"><circle cx="18" cy="18" r="15" fill="none" stroke="var(--icon)" stroke-width="3"/><path d="M18 3v30M5 10l26 16M5 26l26-16" stroke="var(--icon)" stroke-width="2"/></svg>
      <svg width="42" height="22" viewBox="0 0 42 22"><path d="M8 2h20v14H8zM28 7h7l5 5v4H28z" fill="var(--icon)"/><circle cx="13" cy="18" r="3" fill="var(--icon)"/><circle cx="33" cy="18" r="3" fill="var(--icon)"/><path d="M0 6h6M2 10h5" stroke="var(--icon)" stroke-width="2"/></svg>
    </div>
    <div class="coupon">
      <div class="coupon-body">
        <div class="deal">BUY 1<br>PIZZA</div>
        <div class="op">+</div>
        <div class="bonus">
          <svg width="30" height="36" viewBox="0 0 30 36"><path d="M6 10h18l-3 24H9z" fill="var(--badge)"/><rect x="4" y="7" width="22" height="4" fill="var(--badge)"/><path d="M16 7l4-7" stroke="var(--badge)" stroke-width="2"/></svg>
          <span class="free-tag">FREE</span>
        </div>
      </div>
      <div class="coupon-stub">
        <svg width="110" height="80" viewBox="0 0 110 80"><rect x="36" y="18" width="66" height="54" rx="8" fill="none" stroke="var(--stub-ink)" stroke-width="3.5" stroke-dasharray="9 6"/><text x="69" y="55" text-anchor="middle" font-family="Open Sans, sans-serif" font-size="28" font-weight="700" fill="var(--stub-ink)">%</text><circle cx="10" cy="14" r="6" fill="none" stroke="var(--stub-ink)" stroke-width="3"/><circle cx="10" cy="34" r="6" fill="none" stroke="var(--stub-ink)" stroke-width="3"/><path d="M15 17l30 16M15 31l30-16" stroke="var(--stub-ink)" stroke-width="3"/></svg>
      </div>
    </div>
  </section>

  <!-- Offer 2 -->
  <section class="coupon-row" style="top:480px">
    <div class="row-icons">
      <svg width="36" height="36" viewBox="0 0 36 36"><path d="M4 6q14-6 28 0L18 33z" fill="none" stroke="var(--icon)" stroke-width="3" stroke-linejoin="round"/><circle cx="15" cy="13" r="2.5" fill="var(--icon)"/><circle cx="22" cy="18" r="2.5" fill="var(--icon)"/></svg>
      <svg width="42" height="22" viewBox="0 0 42 22"><path d="M8 2h20v14H8zM28 7h7l5 5v4H28z" fill="var(--icon)"/><circle cx="13" cy="18" r="3" fill="var(--icon)"/><circle cx="33" cy="18" r="3" fill="var(--icon)"/><path d="M0 6h6M2 10h5" stroke="var(--icon)" stroke-width="2"/></svg>
    </div>
    <div class="coupon">
      <div class="coupon-body">
        <div class="deal">BUY 2<br>SLICES</div>
        <div class="op">+</div>
        <div class="bonus">
          <svg width="32" height="32" viewBox="0 0 36 36"><path d="M4 6q14-6 28 0L18 33z" fill="none" stroke="var(--badge)" stroke-width="3" stroke-linejoin="round"/><circle cx="15" cy="13" r="2.5" fill="var(--badge)"/><circle cx="22" cy="18" r="2.5" fill="var(--badge)"/></svg>
          <span class="free-tag">FREE</span>
        </div>
      </div>
      <div class="coupon-stub">
        <svg width="110" height="80" viewBox="0 0 110 80"><rect x="36" y="18" width="66" height="54" rx="8" fill="none" stroke="var(--stub-ink)" stroke-width="3.5" stroke-dasharray="9 6"/><text x="69" y="55" text-anchor="middle" font-family="Open Sans, sans-serif" font-size="28" font-weight="700" fill="var(--stub-ink)">%</text><circle cx="10" cy="14" r="6" fill="none" stroke="var(--stub-ink)" stroke-width="3"/><circle cx="10" cy="34" r="6" fill="none" stroke="var(--stub-ink)" stroke-width="3"/><path d="M15 17l30 16M15 31l30-16" stroke="var(--stub-ink)" stroke-width="3"/></svg>
      </div>
    </div>
  </section>

  <!-- Offer 3 -->
  <section class="coupon-row" style="top:620px">
    <div class="row-icons">
      <svg width="36" height="36" viewBox="0 0 36 36"><circle cx="18" cy="18" r="15" fill="none" stroke="var(--icon)" stroke-width="3"/><path d="M18 3v30M5 10l26 16M5 26l26-16" stroke="var(--icon)" stroke-width="2"/></svg>
      <svg width="42" height="22" viewBox="0 0 42 22"><path d="M8 2h20v14H8zM28 7h7l5 5v4H28z" fill="var(--icon)"/><circle cx="13" cy="18" r="3" fill="var(--icon)"/><circle cx="33" cy="18" r="3" fill="var(--icon)"/><path d="M0 6h6M2 10h5" stroke="var(--icon)" stroke-width="2"/></svg>
    </div>
    <div class="coupon">
      <div class="coupon-body">
        <div class="deal">BUY 1<br>PIZZA</div>
        <div class="op">-</div>
        <div class="discount"><div class="pct">20%</div><div class="word">DISCOUNT</div></div>
      </div>
      <div class="coupon-stub">
        <svg width="110" height="80" viewBox="0 0 110 80"><rect x="36" y="18" width="66" height="54" rx="8" fill="none" stroke="var(--stub-ink)" stroke-width="3.5" stroke-dasharray="9 6"/><text x="69" y="55" text-anchor="middle" font-family="Open Sans, sans-serif" font-size="28" font-weight="700" fill="var(--stub-ink)">%</text><circle cx="10" cy="14" r="6" fill="none" stroke="var(--stub-ink)" stroke-width="3"/><circle cx="10" cy="34" r="6" fill="none" stroke="var(--stub-ink)" stroke-width="3"/><path d="M15 17l30 16M15 31l30-16" stroke="var(--stub-ink)" stroke-width="3"/></svg>
      </div>
    </div>
  </section>

  <!-- Offer 4 -->
  <section class="coupon-row" style="top:760px">
    <div class="row-icons">
      <svg width="36" height="36" viewBox="0 0 36 36"><path d="M4 6q14-6 28 0L18 33z" fill="none" stroke="var(--icon)" stroke-width="3" stroke-linejoin="round"/><circle cx="15" cy="13" r="2.5" fill="var(--icon)"/><circle cx="22" cy="18" r="2.5" fill="var(--icon)"/></svg>
      <svg width="42" height="22" viewBox="0 0 42 22"><path d="M8 2h20v14H8zM28 7h7l5 5v4H28z" fill="var(--icon)"/><circle cx="13" cy="18" r="3" fill="var(--icon)"/><circle cx="33" cy="18" r="3" fill="var(--icon)"/><path d="M0 6h6M2 10h5" stroke="var(--icon)" stroke-width="2"/></svg>
    </div>
    <div class="coupon">
      <div class="coupon-body">
        <div class="deal">BUY 3<br>SLICES</div>
        <div class="op">-</div>
        <div class="discount"><div class="pct">30%</div><div class="word">DISCOUNT</div></div>
      </div>
      <div class="coupon-stub">
        <svg width="110" height="80" viewBox="0 0 110 80"><rect x="36" y="18" width="66" height="54" rx="8" fill="none" stroke="var(--stub-ink)" stroke-width="3.5" stroke-dasharray="9 6"/><text x="69" y="55" text-anchor="middle" font-family="Open Sans, sans-serif" font-size="28" font-weight="700" fill="var(--stub-ink)">%</text><circle cx="10" cy="14" r="6" fill="none" stroke="var(--stub-ink)" stroke-width="3"/><circle cx="10" cy="34" r="6" fill="none" stroke="var(--stub-ink)" stroke-width="3"/><path d="M15 17l30 16M15 31l30-16" stroke="var(--stub-ink)" stroke-width="3"/></svg>
      </div>
    </div>
  </section>

  <svg class="nav-settings" width="44" height="44" viewBox="0 0 44 44" aria-label="Settings"><g fill="#2b2b2b"><circle cx="22" cy="22" r="13"/><rect x="18" y="2" width="8" height="40" rx="2"/><rect x="18" y="2" width="8" height="40" rx="2" transform="rotate(45 22 22)"/><rect x="18" y="2" width="8" height="40" rx="2" transform="rotate(90 22 22)"/><rect x="18" y="2" width="8" height="40" rx="2" transform="rotate(135 22 22)"/></g><circle cx="22" cy="22" r="6" fill="var(--screen-bg)"/></svg>

  <svg class="nav-back" width="60" height="34" viewBox="0 0 60 34" aria-label="Back"><path d="M58 17H8M20 4L6 17l14 13" fill="none" stroke="#2b2b2b" stroke-width="5" stroke-linecap="round" stroke-linejoin="round"/></svg>
</main>
</body>
</html>
```